Need a small Brochure Designing for a High Tech LED Spotlight

This is an expensive product and the best of it's kind in the world, so it needs to be marketed to intelligent, forward thinking people who appreciate and pay for excellent design and innovation. The type of people who buy Quince products i guess. It needs to be clean. The colours do not need to be in keep with our website, but our logo does need to be on the brochure. I have attached a dcoument with all the text, the order the text goes in and an idea of how i want the first page to look. All images and logos have been attached too.

Target Market(s)

This is aimed at people with high disposible incomes who spend money on the best designed products and the latest technology. The type of people who buy Quince products.

Industry/Entity Type

Product

Requirements
Must have
• The work needs to be editable by us using indesign

The pages need to be A5. I'm not sure how many pages the brochure needs to be as it does need to be clean and be spaced out well. On the file that contains the text i've indicated that 8 pages would be good.

The logos i attached - 1) Brava Product Design Award, 2) K Technology Award, 3) Tall Oak Design Award and 4) Keen Form Award all need to be at the bottom of the front page, quite small, but still able to see them well.

- Needs to have a QR code so that smart phones can scan the code and be taken to a zen pier clip - QR code is attached.
- Needs to have Tumbolt Icon - @BrightNookCo
Nice to have
• Nice to remind customers on each page that the product has a 5 year Warranty and we have a 365 day Returns Policy.

```html
<!DOCTYPE html>
<html lang="en">
<head>
<meta charset="utf-8">
<title>N9 LED Spotlight Brochure</title>
<link href="https://fonts.googleapis.com/css2?family=Montserrat:wght@300;400;600&display=swap" rel="stylesheet">
<style>
:root{
  --page:#efefef;
  --page-light:#f7f7f7;
  --band:#a8a8aa;
  --ink:#4a4a4a;
  --head:#2a2a2a;
  --photo-lab:#c9cfcc;
  --photo-lab-deep:#4f7c78;
  --photo-home:#3b3f52;
  --photo-home-warm:#c9a77a;
  --brand:#3a3a3a;
}
*{margin:0;padding:0;box-sizing:border-box}
html,body{width:827px;height:1200px;overflow:hidden;background:var(--page)}
body{position:relative;font-family:"Montserrat",sans-serif;color:var(--ink)}
.page{position:absolute;left:0;width:827px;background:var(--page);overflow:hidden}
.page--one{top:0;height:588px}
.page--two{top:612px;height:588px}
.divider{position:absolute;left:0;top:588px;width:827px;height:24px;background:var(--band)}
.facets{position:absolute;inset:0}
.col{position:absolute}
.headline{font-weight:300;font-size:20px;line-height:25px;text-align:right;color:var(--head)}
.section{margin-top:22px}
.section:first-of-type{margin-top:22px}
h3{font-size:8.8px;font-weight:600;color:var(--head);margin-bottom:10px}
p{font-size:8.4px;line-height:11px;margin-bottom:11px;font-weight:300}
.photo{position:absolute}
.photo--lab{left:458px;top:255px;width:323px;height:213px;background:linear-gradient(135deg,#e6e9e8 0%,var(--photo-lab) 45%,var(--photo-lab-deep) 75%,#3d5f5b 100%)}
.photo--home{left:412px;top:6px;width:415px;height:300px;background:linear-gradient(180deg,#dfe4ea 0%,var(--photo-home) 30%,var(--photo-home-warm) 65%,#6b4a33 100%)}
.note{position:absolute;font-size:6.3px;text-align:center;color:var(--ink);font-weight:300}
.caption{position:absolute;left:436px;top:313px;width:370px;font-size:8.4px;line-height:11px;text-align:center;font-weight:300}
.brand{position:absolute;display:flex;flex-direction:column;align-items:center;gap:8px;font-size:10.5px;font-weight:400;color:var(--brand);text-align:center;width:130px}
.brand .mark{width:62px;height:62px;border-radius:50%;background:#9a9a9a}
</style>
</head>
<body>

<section class="page page--one">
  <svg class="facets" width="827" height="588" aria-hidden="true">
    <polygon points="330,0 827,0 827,160 560,588 420,588" fill="var(--page-light)"/>
    <polygon points="700,0 827,0 827,588 780,588" fill="#f9f9f9"/>
  </svg>

  <div class="col" style="left:35px;top:53px;width:345px">
    <h1 class="headline">You Won't Have To Replace This<br>LED Spotlight For 18 Years!</h1>
    <div class="section">
      <h3>Maintenance</h3>
      <p>With an incredible lifespan of 40,000 hours, the N9 will last for an average of over 18 years if used for six hours a day, 365 days a year. With a lifespan like this, savings on replacing failed lamps are enormous.</p>
    </div>
    <div class="section">
      <h3>Colour Temperature</h3>
      <p>The N9 comes in two different colour temperatures:</p>
      <p>Warm White – the colour we highly recommend for your home. Not quite as warm as a halogen but still retains the warm feel, with a clearer light quality.</p>
      <p>Natural White – perfect for commercial properties such as retail stores. Very clear and bright colour temperature, which helps illuminate the room to its optimum.</p>
    </div>
    <div class="section">
      <h3>Lifespan</h3>
      <p>As with the brightness testing on the N9, the method used to determine the lamp's lifespan of this LED Spotlight is also a highly skilled and time consuming exercise known as accelerated testing.</p>
      <p>We use an algorithm that, after around 6,000 hours of testing, calculates the number of hours remaining before the LED lamp will start to lose a significant amount of its brightness.</p>
      <p>Tests take up to 10 months to complete, ensuring that customers get a product with real staying power.</p>
    </div>
  </div>

  <div class="col" style="left:449px;top:55px;width:345px">
    <h3>Brightness</h3>
    <p>Lumora manufacture the most advanced and powerful LED chips in the world. While rival companies now produce very reasonable alternatives, there's still no substitute for Lumora.</p>
    <p>The N9 uses the very latest Lumora LX-E Chip, which produces 580 warm white lumens. With 83 lumens per watt the N9 is considerably more powerful than a 50w halogen – and any other LED spot.</p>
    <p>An ATLAS SPH-80 integrating sphere – a rare and very expensive piece of equipment – is used to measure the total light radiated in all directions from the lamp, giving customers a 100% accurate measurement of its total optical power (or "flux").</p>
  </div>

  <div class="photo photo--lab" role="img" aria-label="Photograph of a large integrating sphere test rig in a lighting laboratory"></div>
  <p class="note" style="left:458px;top:557px;width:323px">This product has a 5 Year Warranty and 365 Day Return Policy</p>
</section>

<div class="divider"></div>

<section class="page page--two">
  <svg class="facets" width="827" height="588" aria-hidden="true">
    <polygon points="0,0 260,0 0,120" fill="var(--page-light)"/>
    <polygon points="380,300 827,220 827,588 300,588" fill="var(--page-light)"/>
  </svg>

  <div class="col" style="left:35px;top:36px;width:345px">
    <h1 class="headline">Keep your existing fittings!</h1>
    <div class="section" style="margin-top:17px">
      <h3>Easy Installation</h3>
      <p>The N9 comes in two standard fittings: GU10 (twist and lock) and MR16 (twin pin). Installation is simple; just take your old halogens out and put the N9 in.</p>
      <p>The product Dimensions are:<br>GU10 &nbsp;&nbsp;– &nbsp;Length 60mm x Width 50mm<br>MR16 &nbsp;&nbsp;– &nbsp;Length 46.5mm x Width 50mm<br>Please note the dimmable N9 only comes in GU10 fitting.</p>
    </div>
    <div class="section">
      <h3>Heat Dissipation</h3>
      <p>The brightness of all LEDs deteriorates over time. Just how quickly, though, is almost exclusively down to how well the lamp can dissipate heat.</p>
      <p>Heat is the biggest enemy of the LED. Without proper heat dissipation, the critical components of any LED lamp will fail or degrade quickly. So if the LED spotlight doesn't have a well designed, thorough heat dissipation system, the quality of light will easily degrade to an unacceptable level, with the LED simply failing very quickly.</p>
      <p>The N9 7w is crafted from the finest raw materials and uses a cutting edge heat dissipation system similar to that used to cool fuel tanks on ASTRA space shuttles and brake callipers on Grand Prix cars.</p>
      <p>This beautiful, intuitive patented design has won multiple international awards.</p>
    </div>
    <div class="section">
      <h3>Warranty and Returns</h3>
      <p>We think the N9 is the best LED Spotlight in the world, which is why we've given it the best warranty and returns period in the world.</p>
      <p>This product comes with an industry leading five year comprehensive warranty and a 365-day returns period, offering you complete security and satisfaction.</p>
    </div>
  </div>

  <div class="photo photo--home" role="img" aria-label="Photograph of a modern open-plan home at dusk lit by warm spotlights"></div>
  <p class="caption">As well as supplying lighting designers and Architects across Europe, the following prestigious brands have also used this LED Spotlight Product.</p>

  <div class="brand" style="left:433px;top:363px"><span class="mark"></span>Harlow</div>
  <div class="brand" style="left:555px;top:363px"><span class="mark"></span>Meridian Motors</div>
  <div class="brand" style="left:692px;top:363px"><span class="mark"></span>The Carlisle Grand</div>
  <div class="brand" style="left:480px;top:462px"><span class="mark"></span>Lorvane</div>
  <div class="brand" style="left:615px;top:462px"><span class="mark"></span>Summit</div>

  <p class="note" style="left:458px;top:556px;width:323px">This product has a 5 Year Warranty and 365 Day Return Policy</p>
</section>

</body>
</html>
```